Online business manager needs a website

I need a website designed and then coded. I am an online business manager serving a number of different industries providing administrative support to existing small businesses and helping solo practitioners get their new business up and running.

I didn't have a logo formally designed but have been using the attached avatar and wouldn't mind something that incorporated that.

The business doesn't have an official name, so I've just been using my name Lena Morvath, Online Business Manager or Lena Morvath, OBM. I've attached two documents that I have made previously for an example of content.

I would prefer the final site be in Wordpress.

Requirements
Must have
• A way to contact me, testimonials, list of services

```html
<!DOCTYPE html>
<html lang="en">
<head>
<meta charset="utf-8">
<title>Lena Morvath — Online Business Manager</title>
<link href="https://fonts.googleapis.com/css2?family=Outfit:wght@200;300;400;500;600;700&display=swap" rel="stylesheet">
<style>
:root{
  --navy:#0a0d2c;
  --navy-mid:#16205a;
  --blue:#3b6fd8;
  --teal:#2bd6cf;
  --ink:#1b1d26;
  --text:#3c3f4a;
  --muted:#8a8f9c;
  --line:#d9dce3;
  --grey-bg:#f0f2f5;
  --white:#ffffff;
  --coral:#f2b8a0;
}
*{box-sizing:border-box;margin:0;padding:0}
html,body{width:1200px;height:3916px;overflow:hidden}
body{position:relative;font-family:"Outfit",sans-serif;color:var(--text);background:var(--white)}
.abs{position:absolute}
a{color:inherit;text-decoration:none}

/* shared */
.section-title{position:absolute;left:0;width:1200px;text-align:center;font-size:36px;font-weight:300;color:var(--ink);letter-spacing:-.3px}
.section-title b{font-weight:600}
.outline-btn{position:absolute;display:flex;align-items:center;justify-content:center;border:1.5px solid var(--blue);border-radius:20px;font-size:12.5px;color:var(--blue);background:transparent}
.star{position:absolute;width:3px;height:3px;border-radius:50%;background:#5a8cff;opacity:.8}

/* hero */
.hero{position:absolute;left:0;top:0;width:1200px;height:580px}
.hero-bg{position:absolute;inset:0}
.brand{position:absolute;display:flex;align-items:center;gap:10px}
.brand-avatar{width:50px;height:46px;border-radius:8px;background:linear-gradient(135deg,#f0c27a,#7fb3d8)}
.brand-name{font-size:20px;font-weight:600;letter-spacing:1.5px;color:var(--teal);line-height:1}
.brand-role{font-size:12.5px;color:var(--white);margin-top:4px}
.nav{position:absolute;top:23px;left:543px;display:flex;align-items:center;font-size:13px;color:var(--white)}
.nav span{position:absolute;top:9px;white-space:nowrap}
.nav .active{color:var(--teal)}
.nav .active::after{content:"";position:absolute;left:50%;top:24px;width:12px;height:1.5px;margin-left:-6px;background:var(--teal)}
.nav-btn{position:absolute;left:917px;top:23px;width:121px;height:34px;border:1.5px solid var(--teal);border-radius:18px;display:flex;align-items:center;justify-content:center;font-size:13px;color:var(--white)}
.hero-first{position:absolute;left:158px;top:148px;font-size:76px;font-weight:200;color:var(--white);letter-spacing:2px;line-height:1}
.hero-last{position:absolute;left:156px;top:222px;font-size:84px;font-weight:700;color:var(--white);letter-spacing:1px;line-height:1}
.hero-badge{position:absolute;left:161px;top:327px;width:315px;height:33px;background:linear-gradient(90deg,var(--blue),var(--teal));display:flex;align-items:center;justify-content:center;font-size:14.5px;letter-spacing:3px;color:var(--white);font-weight:400}
.hero-text{position:absolute;left:161px;top:380px;width:390px;font-size:12.5px;line-height:24px;color:#e6e9f5}
.hero-photo{position:absolute;left:635px;top:114px;width:396px;height:396px;border-radius:50%;background:radial-gradient(circle at 50% 45%,#d9a577,#8a7a68 60%,#4a4f5c)}
.hero-ring{position:absolute;left:626px;top:104px;width:414px;height:414px;border-radius:50%;border:2px solid #3fa3e0}
.hero-ring2{position:absolute;left:620px;top:98px;width:426px;height:426px;border-radius:50%;border:1px solid rgba(63,163,224,.35)}

/* about */
.monitor-screen{position:absolute;left:161px;top:704px;width:374px;height:260px;background:#2b2b30;border-radius:10px}
.monitor-photo{position:absolute;left:175px;top:718px;width:346px;height:200px;background:linear-gradient(135deg,#c94a86,#7a4a5c 45%,#e3b79a 70%,#3f7a3b)}
.monitor-head{position:absolute;left:270px;top:652px;width:150px;height:160px;border-radius:60px 60px 20px 20px;background:linear-gradient(#d8aa7c,#e1b693)}
.monitor-chin{position:absolute;left:161px;top:932px;width:374px;height:32px;background:linear-gradient(#e6e8ec,#c9ccd3);border-radius:0 0 10px 10px}
.monitor-stand{position:absolute;left:298px;top:964px;width:100px;height:48px;background:linear-gradient(#cfd2d8,#eef0f3);clip-path:polygon(18% 0,82% 0,100% 100%,0 100%)}
.about-title{position:absolute;left:610px;top:662px;font-size:35px;font-weight:300;color:var(--ink)}
.about-title b{font-weight:600}
.about-sub{position:absolute;left:611px;top:712px;font-size:12.5px;letter-spacing:2.5px;color:var(--ink);font-weight:500}
.about-text{position:absolute;left:611px;top:741px;width:430px;font-size:12.2px;line-height:25.6px;color:var(--text)}
.fill-btn{position:absolute;left:611px;top:994px;width:135px;height:37px;border-radius:20px;background:linear-gradient(90deg,var(--blue),var(--teal));color:var(--white);font-size:12.5px;display:flex;align-items:center;justify-content:center}

/* services */
.services{position:absolute;left:0;top:1106px;width:1200px;height:660px;background:var(--grey-bg)}
.card{position:absolute;top:1243px;width:203px;height:353px;background:var(--white);border:1px solid #e1e4ea}
.card-img{height:143px;background:#bfc6d2}
.card-icon{position:absolute;left:71px;top:112px;width:60px;height:60px;border-radius:50%;background:linear-gradient(135deg,var(--blue),var(--teal));border:3px solid var(--white);display:flex;align-items:center;justify-content:center}
.card h3{margin-top:45px;text-align:center;font-size:13.5px;font-weight:600;color:var(--ink);line-height:21px;padding:0 14px}
.card ul{list-style:none;margin-top:4px;text-align:center;font-size:11.3px;line-height:22.6px;color:var(--text);padding:0 10px}

/* work */
.work-card{position:absolute;top:1874px;width:278px;height:278px}
.work-cap{position:absolute;top:2172px;width:278px;text-align:center}
.work-cap b{display:block;font-size:13.5px;font-weight:600;color:var(--white)}
.work-cap span{display:block;font-size:12px;color:#d9ddea;margin-top:6px}
.arrow{position:absolute;width:36px;height:36px;border-radius:50%;display:flex;align-items:center;justify-content:center}

/* logos */
.logo-item{position:absolute;top:2416px;display:flex;align-items:center;gap:8px;font-size:20px;font-weight:500;color:#8c909a}
.logo-dot{width:24px;height:24px;border-radius:50%;background:#9a9ea8}

/* testimonials */
.quote-card{position:absolute;top:2663px;width:428px;height:271px;background:var(--white);box-shadow:0 4px 18px rgba(20,30,60,.08);border:1px solid #eceef2}
.quote-card p{position:absolute;left:30px;top:55px;width:368px;text-align:center;font-size:12.2px;line-height:25.6px;color:var(--text)}
.quote-name{position:absolute;left:0;top:196px;width:100%;text-align:center;font-size:12.3px;letter-spacing:1.5px;font-weight:600;color:var(--ink)}
.quote-co{position:absolute;left:0;top:222px;width:100%;text-align:center;font-size:12px;color:var(--text)}
.quote-avatar{position:absolute;left:175px;top:-38px;width:78px;height:78px;border-radius:50%;background:linear-gradient(135deg,#e9c38f,#9ccf9a);border:3px solid var(--white);box-shadow:0 0 0 2px #3fa3e0}
.dot{position:absolute;top:2966px;width:7px;height:7px;border-radius:50%;background:#b9d3f1}

/* contact */
.touch-bg{position:absolute;left:0;top:3048px;width:1200px;height:620px;background:var(--grey-bg)}
.form-box{position:absolute;left:161px;top:3188px;width:525px;height:365px;background:var(--white)}
.field{position:absolute;font-size:11.5px;color:var(--muted);border-bottom:1px solid var(--line);height:36px;padding-top:10px}
.field.active{color:var(--ink);border-bottom:1.5px solid var(--blue)}
.info-box{position:absolute;left:686px;top:3188px;width:352px;height:365px;background:linear-gradient(160deg,#3a78d8,#2dc4d6 70%,#2ad9cc)}
.info-row{position:absolute;left:48px;display:flex;align-items:center;gap:14px;font-size:13px;font-weight:500;color:var(--white)}
.info-icon{width:32px;height:32px;border-radius:50%;background:var(--white);display:flex;align-items:center;justify-content:center}

/* footer */
.footer-nav{position:absolute;top:3789px;left:0;width:1200px;display:flex;justify-content:center;gap:31px;font-size:13px;color:var(--white)}
.copyright{position:absolute;top:3878px;left:0;width:1200px;text-align:center;font-size:12px;color:#cfd4e6}
</style>
</head>
<body>

<!-- HERO -->
<section class="hero">
  <svg class="hero-bg" width="1200" height="580" viewBox="0 0 1200 580" aria-hidden="true">
    <defs>
      <radialGradient id="heroGrad" cx="0.5" cy="0.85" r="0.75">
        <stop offset="0" stop-color="#1b2a78"/>
        <stop offset="0.55" stop-color="#0f1648"/>
        <stop offset="1" stop-color="#070a24"/>
      </radialGradient>
    </defs>
    <path d="M0 0H1200V500Q600 650 0 500Z" fill="url(#heroGrad)"/>
  </svg>
  <span class="star" style="left:118px;top:130px"></span>
  <span class="star" style="left:460px;top:470px"></span>
  <span class="star" style="left:1080px;top:170px"></span>
  <span class="star" style="left:575px;top:90px"></span>
  <span class="star" style="left:1110px;top:420px"></span>

  <div class="brand" style="left:158px;top:18px">
    <div class="brand-avatar" role="img" aria-label="Cartoon avatar of Lena at her laptop"></div>
    <div>
      <div class="brand-name">LENA MORVATH</div>
      <div class="brand-role">Online Business Manager</div>
    </div>
  </div>
  <nav class="nav">
    <span class="active" style="left:0">Home</span>
    <span style="left:67px">About Me</span>
    <span style="left:156px">What I Do Best</span>
    <span style="left:279px">Client Love</span>
  </nav>
  <a class="nav-btn" href="#contact">Contact Me</a>

  <div class="hero-first">LENA</div>
  <div class="hero-last">MORVATH</div>
  <div class="hero-badge">DIGITAL BUSINESS MANAGER</div>
  <p class="hero-text">Focused on the live event and entertainment industry. Helping artists and owners to better manage their career and business by strategically reviewing systems, recommending operational efficiencies, and managing inboxes.</p>

  <div class="hero-ring2"></div>
  <div class="hero-ring"></div>
  <div class="hero-photo" role="img" aria-label="Portrait photo of Lena smiling outdoors on a city street"></div>
</section>

<!-- ABOUT -->
<section class="about">
  <div class="monitor-screen"></div>
  <div class="monitor-photo" role="img" aria-label="Photo of Lena in glasses in front of pink flowers, shown on a desktop monitor"></div>
  <div class="monitor-chin"></div>
  <div class="monitor-stand"></div>

  <h2 class="about-title">About <b>Me</b></h2>
  <div class="about-sub">LENA MORVATH, VIRTUAL ASSISTANT</div>
  <p class="about-text">Hi! I'm so excited that you have chosen to explore my portfolio. Helping businesses achieve their goals is my passion, and I'm thrilled that with my assistance you will have more time for your own passion project. I thrive while working independently, which means you can be confident when leaving tasks for me. The type of work that lights me up is anything involving organization and/or spreadsheets. You need data analyzed that includes multiple nested if formulas? You have an overwhelming amount of email to sort through and appointments to book? I'm your gal!</p>
  <a class="fill-btn" href="#contact">Contact Me</a>
</section>

<!-- SERVICES -->
<section>
  <div class="services"></div>
  <h2 class="section-title" style="top:1170px">What I <b>Do Best</b></h2>

  <article class="card" style="left:161px">
    <div class="card-img" role="img" aria-label="Photo of an assistant with a headset working at a laptop" style="background:linear-gradient(135deg,#d9dde3,#a8aeb8)"></div>
    <div class="card-icon"><svg width="26" height="26" viewBox="0 0 24 24" fill="none" stroke="#fff" stroke-width="1.8"><path d="M4 14v-2a8 8 0 0 1 16 0v2"/><rect x="3" y="13" width="4" height="6" rx="1.5"/><rect x="17" y="13" width="4" height="6" rx="1.5"/></svg></div>
    <h3>Virtual Assistance</h3>
    <ul><li>Calendar Management</li><li>Email Management</li><li>Light Graphic Design</li><li>Data Entry</li></ul>
  </article>

  <article class="card" style="left:386px">
    <div class="card-img" role="img" aria-label="Photo of a person editing content on a computer screen" style="background:linear-gradient(135deg,#3c4a66,#9aa5b8 55%,#d8c2a6)"></div>
    <div class="card-icon"><svg width="26" height="26" viewBox="0 0 24 24" fill="none" stroke="#fff" stroke-width="1.8"><rect x="4" y="4" width="16" height="16" rx="2"/><path d="M8 9h8M8 13h8M8 17h5"/></svg></div>
    <h3>Social Media &amp; Content Management</h3>
    <ul><li>Content Repurposing</li><li>Graphics Creation</li><li>Audiogram Creation</li><li>Search Engine Optimization</li></ul>
  </article>

  <article class="card" style="left:610px">
    <div class="card-img" role="img" aria-label="Photo of colourful finance charts on a tablet" style="background:linear-gradient(135deg,#e6ebf2,#b9c4d6 60%,#8ea0c2)"></div>
    <div class="card-icon"><svg width="26" height="26" viewBox="0 0 24 24" fill="none" stroke="#fff" stroke-width="1.8"><path d="M4 20h16"/><rect x="6" y="12" width="3" height="6"/><rect x="11" y="8" width="3" height="10"/><rect x="16" y="5" width="3" height="13"/></svg></div>
    <h3>Finance Management</h3>
    <ul><li>Create Invoices</li><li>Track Receivables</li><li>Analyze Expenses</li><li>Year Over Year Analytics</li></ul>
  </article>

  <article class="card" style="left:835px">
    <div class="card-img" role="img" aria-label="Photo of two colleagues in a business meeting" style="background:linear-gradient(135deg,#c8ccd4,#5a606e 60%,#2c3140)"></div>
    <div class="card-icon"><svg width="26" height="26" viewBox="0 0 24 24" fill="none" stroke="#fff" stroke-width="1.8"><circle cx="12" cy="12" r="3.2"/><circle cx="12" cy="12" r="7.5"/><path d="M12 2v3M12 19v3M2 12h3M19 12h3"/></svg></div>
    <h3>Business Management</h3>
    <ul><li style="line-height:18px;padding:2px 0">Creation of Operating Procedures</li><li>Review of Website Strategy</li><li>Reporting and Analytics</li><li>Project Management</li></ul>
  </article>

  <a class="outline-btn" href="#contact" style="left:532px;top:1627px;width:135px;height:38px">Contact Me</a>
</section>

<!-- MY WORK -->
<section>
  <svg class="abs" style="left:0;top:1730px" width="1200" height="636" viewBox="0 0 1200 636" aria-hidden="true">
    <defs>
      <radialGradient id="workGrad" cx="0.5" cy="0.05" r="0.9">
        <stop offset="0" stop-color="#1c2c7c"/>
        <stop offset="0.5" stop-color="#0e1545"/>
        <stop offset="1" stop-color="#070a22"/>
      </radialGradient>
    </defs>
    <path d="M0 80Q600 -50 1200 80V636H0Z" fill="url(#workGrad)"/>
  </svg>
  <span class="star" style="left:818px;top:1776px"></span>
  <span class="star" style="left:120px;top:2245px"></span>
  <span class="star" style="left:1070px;top:1940px"></span>

  <h2 class="section-title" style="top:1800px;color:#fff">My <b>Work</b></h2>

  <div class="arrow" style="left:87px;top:1996px;border:1.5px solid var(--teal)"><svg width="14" height="14" viewBox="0 0 24 24" fill="none" stroke="#2bd6cf" stroke-width="2"><path d="M19 12H5M11 6l-6 6 6 6"/></svg></div>
  <div class="arrow" style="left:1075px;top:1996px;border:1.5px solid #4a5170"><svg width="14" height="14" viewBox="0 0 24 24" fill="none" stroke="#8c93ad" stroke-width="2"><path d="M5 12h14M13 6l6 6-6 6"/></svg></div>

  <div class="work-card" style="left:161px;background:linear-gradient(135deg,#f8e3d6,#f3d0bd 60%,#e9b79c)" role="img" aria-label="Promotional graphic for a talk on owning business workflows and automations"></div>
  <div class="work-card" style="left:461px;background:#f4585a" role="img" aria-label="Coral quote graphic for a social media post"></div>
  <div class="work-card" style="left:760px;background:linear-gradient(135deg,#f6f1ec,#e8ddd5);border:6px solid #2b2560" role="img" aria-label="Podcast episode promotional graphic"></div>

  <div class="work-cap" style="left:161px"><b>Lorem Ipsum Dolor</b><span>Lorem Ipsum is simply dummy text</span></div>
  <div class="work-cap" style="left:461px"><b>Lorem Ipsum Dolor</b><span>Lorem Ipsum is simply dummy text</span></div>
  <div class="work-cap" style="left:760px"><b>Lorem Ipsum Dolor</b><span>Lorem Ipsum is simply dummy text</span></div>

  <a class="outline-btn" href="#" style="left:521px;top:2253px;width:157px;height:37px;border-color:var(--teal);color:#fff">View More Work</a>
</section>

<!-- CLIENT LOGOS -->
<section>
  <div class="logo-item" style="left:161px"><span class="logo-dot"></span>Halden</div>
  <div class="logo-item" style="left:336px">Northvale</div>
  <div class="logo-item" style="left:522px"><span class="logo-dot"></span>Corrin</div>
  <div class="logo-item" style="left:700px"><span class="logo-dot"></span>Brightmere</div>
  <div class="logo-item" style="left:895px;letter-spacing:3px;font-weight:400">OSTRA</div>
  <div class="abs" style="left:161px;top:2486px;width:878px;height:1px;background:#e3e5ea"></div>
</section>

<!-- CLIENT LOVE -->
<section>
  <h2 class="section-title" style="top:2552px">Client <b>Love</b></h2>

  <div class="arrow" style="left:87px;top:2781px;border:1.5px solid #d5d8de"><svg width="14" height="14" viewBox="0 0 24 24" fill="none" stroke="#b6bac3" stroke-width="2"><path d="M19 12H5M11 6l-6 6 6 6"/></svg></div>
  <div class="arrow" style="left:1075px;top:2781px;border:1.5px solid #3fa3e0"><svg width="14" height="14" viewBox="0 0 24 24" fill="none" stroke="#3fa3e0" stroke-width="2"><path d="M5 12h14M13 6l6 6-6 6"/></svg></div>

  <article class="quote-card" style="left:161px">
    <div class="quote-avatar" role="img" aria-label="Client portrait photo"></div>
    <p>“When it became apparent that a project would take more time than I had, Lena stepped up to take on the required research. She was thorough and timely; able to meet a last-minute 12-hour deadline. I would highly recommend Lena to assist with your next project.”</p>
    <div class="quote-name">- DARA P. WELLS</div>
    <div class="quote-co">Summit Ridge Roofing</div>
  </article>
  <article class="quote-card" style="left:610px">
    <div class="quote-avatar" role="img" aria-label="Client portrait photo"></div>
    <p>“When it became apparent that a project would take more time than I had, Lena stepped up to take on the required research. She was thorough and timely; able to meet a last-minute 12-hour deadline. I would highly recommend Lena to assist with your next project.”</p>
    <div class="quote-name">- DARA P. WELLS</div>
    <div class="quote-co">Summit Ridge Roofing</div>
  </article>

  <span class="dot" style="left:566px"></span>
  <span class="dot" style="left:585px;top:2964px;width:10px;height:10px;background:none;border:2px solid #3fa3e0"></span>
  <span class="dot" style="left:606px"></span>
  <span class="dot" style="left:626px"></span>
</section>

<!-- GET IN TOUCH -->
<section id="contact">
  <div class="touch-bg"></div>
  <h2 class="section-title" style="top:3114px">Get In <b>Touch</b></h2>

  <form class="form-box">
    <div class="field active" style="left:52px;top:42px;width:202px">Maren |</div>
    <div class="field" style="left:277px;top:42px;width:202px">Last Name</div>
    <div class="field" style="left:52px;top:104px;width:202px">Email Address</div>
    <div class="field" style="left:277px;top:104px;width:202px">Phone Number</div>
    <div class="field" style="left:52px;top:164px;width:427px;height:89px">Message</div>
    <div class="outline-btn" style="left:53px;top:277px;width:151px;height:36px">Send Message</div>
  </form>

  <div class="info-box">
    <div class="brand" style="left:46px;top:54px">
      <div class="brand-avatar" role="img" aria-label="Cartoon avatar of Lena at her laptop" style="width:54px;height:46px"></div>
      <div>
        <div class="brand-name" style="color:#fff;font-size:21px">LENA MORVATH</div>
        <div class="brand-role" style="color:#eaf4ff">Online Business Manager</div>
      </div>
    </div>
    <div class="info-row" style="top:125px"><span class="info-icon"><svg width="14" height="14" viewBox="0 0 24 24" fill="none" stroke="#3b6fd8" stroke-width="2"><rect x="7" y="2" width="10" height="20" rx="2"/><path d="M11 18h2"/></svg></span>555.014.2286</div>
    <div class="info-row" style="top:171px"><span class="info-icon"><svg width="14" height="14" viewBox="0 0 24 24" fill="none" stroke="#3b6fd8" stroke-width="2"><rect x="3" y="5" width="18" height="14" rx="2"/><path d="M3 7l9 6 9-6"/></svg></span>lena.obm@mailbox.test</div>
    <div class="info-row" style="top:215px"><span class="info-icon"></span>Lena Ruth Morvath</div>
    <div class="info-row" style="top:260px"><span class="info-icon"></span>/LenaRuth07</div>
  </div>
</section>

<!-- FOOTER -->
<footer>
  <svg class="abs" style="left:0;top:3616px" width="1200" height="300" viewBox="0 0 1200 300" aria-hidden="true">
    <defs>
      <radialGradient id="footGrad" cx="0.5" cy="0.1" r="0.9">
        <stop offset="0" stop-color="#18246a"/>
        <stop offset="0.6" stop-color="#0c1240"/>
        <stop offset="1" stop-color="#070a22"/>
      </radialGradient>
    </defs>
    <path d="M0 80Q600 -40 1200 80V300H0Z" fill="url(#footGrad)"/>
  </svg>
  <span class="star" style="left:120px;top:3796px"></span>
  <span class="star" style="left:1080px;top:3700px"></span>

  <div class="brand" style="left:477px;top:3700px">
    <div class="brand-avatar" role="img" aria-label="Cartoon avatar of Lena at her laptop" style="width:62px;height:52px"></div>
    <div>
      <div class="brand-name" style="color:#fff;font-size:23px">LENA MORVATH</div>
      <div class="brand-role" style="font-size:14px">Online Business Manager</div>
    </div>
  </div>
  <nav class="footer-nav">
    <span style="color:var(--teal)">Home</span>
    <span>About Me</span>
    <span>What I Do Best</span>
    <span>Client Love</span>
    <span>Contact Me</span>
  </nav>
  <div class="copyright">© 2023 Lena Morvath. All Rights Reserved.</div>
</footer>

</body>
</html>
```